Halvery Construction Group Website

Need a dynamic corporate website that can be built on with time. We want to get our information out to the world and have a place where customers can submit requests for proposals.

Target Market(s)

Custom home owners and buyers. Architects and Real Estate Agents.

Industry/Entity Type

Construction

Number of Pages Required

3 page

Font styles to use
Serif
Sans Serif

Requirements
Must have
• Company logo, about, company contact information, biography, contact, projects,
• Sleek, modern, clean, attractive design.
• Online form customers can use for filling out a request for project proposal.
• Linkedin hyperlink.
• Uses www.halveryconstructiongroup.example

```html
<!DOCTYPE html>
<html lang="en">
<head>
<meta charset="utf-8">
<title>Halvery Construction Group</title>
<link rel="stylesheet" href="https://fonts.googleapis.com/css2?family=Aldrich&family=Arimo:wght@400&display=swap">
<style>
:root{
  --hero-dark:#1f5aa6;
  --hero-deep:#0c3f88;
  --hero-light:#3fa6e6;
  --hero-sky:#1aa0e6;
  --white:#ffffff;
  --nav-active:#0d4a97;
  --panel:#f4f6f9;
  --heading:#5a5f66;
  --body:#7a7f86;
  --link-blue:#0d4a97;
  --bar:#004c99;
}
*{margin:0;padding:0;box-sizing:border-box}
html,body{width:1200px;height:909px;overflow:hidden;background:var(--panel)}
body{position:relative;font-family:"Arimo",Arial,sans-serif}
.hero{position:absolute;left:0;top:0;width:1200px;height:608px;overflow:hidden}
.hero-interior{position:absolute;inset:0;background:linear-gradient(160deg,var(--hero-dark) 0%,#1b4f98 55%,var(--hero-deep) 100%)}
.hero-city{position:absolute;inset:0;background:linear-gradient(180deg,var(--hero-sky) 0%,var(--hero-light) 45%,#2d86d6 100%);clip-path:polygon(542px 0,1200px 0,1200px 608px,668px 608px)}
.brand{position:absolute;left:87px;top:45px;display:flex;align-items:center;gap:12px;color:var(--white);font-family:"Aldrich",sans-serif}
.brand-square{width:56px;height:56px;border:3px solid var(--white)}
.brand-name{font-size:36px;line-height:36px;letter-spacing:1px}
.brand-sub{font-size:11.5px;line-height:14px;letter-spacing:.3px}
.nav{position:absolute;top:63px;left:0;font-family:"Aldrich",sans-serif;font-size:14px;color:var(--white)}
.nav a{position:absolute;color:inherit;text-decoration:none;white-space:nowrap}
.nav a.active{color:var(--nav-active)}
.search{position:absolute;left:1067px;top:48px;width:48px;height:48px;border:2px solid var(--white);border-radius:50%}
.hero-mark{position:absolute;left:0;width:1200px;top:296px;text-align:center;font-family:"Aldrich",sans-serif;font-size:30px;color:var(--white);letter-spacing:2px}
.col-title{position:absolute;top:641px;font-family:"Aldrich",sans-serif;font-size:18px;color:var(--heading);white-space:nowrap}
.list{position:absolute;top:680px;list-style:none;font-size:12.5px;color:var(--body)}
.list li{height:28.3px;padding-left:19px;position:relative}
.list li::before{content:"»";position:absolute;left:0;top:-1px;font-size:12px}
.about-text{position:absolute;left:578px;top:679px;width:520px;font-size:12.5px;line-height:24px;color:var(--body)}
.more{position:absolute;left:580px;top:789px;font-family:"Aldrich",sans-serif;font-size:12.5px;color:var(--link-blue);text-decoration:underline}
.bar{position:absolute;left:0;top:848px;width:1200px;height:61px;background:var(--bar)}
.copy{position:absolute;left:87px;top:22px;font-size:12.5px;color:var(--white)}
.social{position:absolute;top:12px;width:37px;height:37px;border:2px solid var(--white);border-radius:50%}
</style>
</head>
<body>
<section class="hero">
  <div class="hero-interior" role="img" aria-label="Photo of a modern dining room interior in blue tones"></div>
  <div class="hero-city" role="img" aria-label="Photo of a city skyline with high-rise towers in bright blue tones"></div>
  <div class="brand">
    <div class="brand-square"></div>
    <div>
      <div class="brand-name">HALVERY</div>
      <div class="brand-sub">CONSTRUCTION GROUP, INC.</div>
    </div>
  </div>
  <nav class="nav">
    <a class="active" style="left:603px">HOME</a>
    <a style="left:688px">ABOUT</a>
    <a style="left:780px">BIO</a>
    <a style="left:848px">PROJECTS</a>
    <a style="left:964px">CONTACT US</a>
  </nav>
  <div class="search">
    <svg width="44" height="44" viewBox="0 0 44 44"><circle cx="21" cy="21" r="4.5" fill="none" stroke="#fff" stroke-width="2"/><line x1="24.5" y1="24.5" x2="27.5" y2="27.5" stroke="#fff" stroke-width="2.4" stroke-linecap="round"/></svg>
  </div>
  <div class="hero-mark">HALVERY</div>
</section>

<h2 class="col-title" style="left:86px">PROJECTS</h2>
<ul class="list" style="left:86px"><li>New construction</li><li>Renovations</li><li>Site works</li></ul>
<h2 class="col-title" style="left:250px">PROFILE</h2>
<ul class="list" style="left:250px"><li>Team</li><li>Process</li><li>Testimonials</li><li>History</li></ul>
<h2 class="col-title" style="left:404px">CONNECT</h2>
<ul class="list" style="left:404px"><li>Home</li><li>About</li><li>Bio</li><li>Projects</li><li>Contact us</li></ul>
<h2 class="col-title" style="left:577px">COMMERCIAL, RESIDENTIAL AND COMMUNITY SOLUTIONS</h2>
<p class="about-text">Sed ut perspiciatis unde omnis iste natus error sit voluptatem accusantium doloremque laudan tium, totam rem aperiam, eaque ipsa quae ab illo inventore veritatis et quasi architecto beatae vit ae dicta sunt explicabo. Nemo enim ipsam voluptatem quia voluptas sit aspernatur aut dolores eos qui ratione voluptatem sequi nesciunt.</p>
<a class="more">READ MORE INFO</a>

<footer class="bar">
  <p class="copy">© 2016 Copyrights.Halvery Construction Group.All Rights Reserved.</p>
  <span class="social" style="left:907px"></span>
  <span class="social" style="left:950px"></span>
  <span class="social" style="left:992px"></span>
  <span class="social" style="left:1035px"></span>
  <span class="social" style="left:1078px"></span>
</footer>
</body>
</html>
```